Oil Field Service company needs professional business cards

Looking to clean up our current company business cards and look a little more professional. Brenwick Casing Services is a US based company that services the oil field. We deal with engineers, managers and oil rigs....................................................................................................................................................................................................................................................................................................................................................................................................

Target Market(s)

Oil and Gas professionals

Industry/Entity Type

Oil And Gas

Contact Information for Business Card

See attached photo as example

Font styles to use
Sans Serif

Colors
ec1f27

Requirements
Must have
• Company Logo, Name, Title, Cell, Office, Fax, Email.
• See attached photo
Nice to have
• External CRT, Internal CRT, Casing Crews, Torque Turn, Laydown Machine
Should not have
• Do not introduce any new pictures and keep it professional looking

```html
<!DOCTYPE html>
<html lang="en">
<head>
<meta charset="utf-8">
<title>Brenwick Casing Services – Business Card</title>
<link rel="stylesheet" href="https://fonts.googleapis.com/css2?family=Open+Sans:wght@400;600;700&display=swap">
<style>
  :root {
    --brand-red: #ec1f27;
    --slate: #3d4a57;
    --card-back: #3f4c59;
    --ink: #1f1f1f;
    --light-text: #e6e9ec;
    --white: #ffffff;
    --bg-top: #2b2b2b;
    --bg-bottom: #050505;
  }
  * { margin: 0; padding: 0; box-sizing: border-box; }
  html, body { width: 1200px; height: 900px; overflow: hidden; }
  body {
    position: relative;
    background: linear-gradient(180deg, var(--bg-top) 0%, #141414 55%, var(--bg-bottom) 100%);
    font-family: "Open Sans", Arial, sans-serif;
  }
  .card {
    position: absolute;
    top: 306px;
    width: 440px;
    height: 271px;
    border-radius: 12px;
    overflow: hidden;
  }
  .card-front { left: 149px; background: var(--white); }
  .card-back { left: 608px; background: var(--card-back); }

  .wordmark {
    font-weight: 700;
    text-transform: uppercase;
    line-height: 1.15;
  }
  .card-front .wordmark {
    position: absolute;
    right: 32px;
    top: 44px;
    color: var(--slate);
    font-size: 21px;
    letter-spacing: 2px;
    text-align: center;
  }
  .holder-name {
    position: absolute;
    left: 31px;
    top: 105px;
    color: var(--brand-red);
    font-size: 16px;
    font-weight: 700;
  }
  .holder-title {
    position: absolute;
    left: 31px;
    top: 125px;
    color: var(--ink);
    font-size: 12px;
  }
  .divider {
    position: absolute;
    left: 28px;
    top: 162px;
    width: 385px;
    height: 1px;
    background: var(--brand-red);
  }
  .contact-list {
    position: absolute;
    right: 31px;
    top: 181px;
    list-style: none;
    text-align: right;
    font-size: 12px;
    color: var(--ink);
  }
  .contact-list li { height: 16px; line-height: 16px; }
  .contact-list svg { width: 9px; height: 9px; margin-left: 3px; vertical-align: -1px; fill: var(--brand-red); }
  .address {
    position: absolute;
    left: 27px;
    top: 229px;
    font-size: 12px;
    color: var(--ink);
  }

  .card-back .wordmark {
    position: absolute;
    left: 0; right: 0;
    top: 96px;
    color: var(--white);
    font-size: 28px;
    letter-spacing: 3px;
    text-align: center;
  }
  .service-list {
    position: absolute;
    left: 0; right: 0;
    list-style: none;
    text-align: center;
    font-size: 12px;
    color: var(--light-text);
  }
  .service-list.row-one { top: 208px; }
  .service-list.row-two { top: 231px; }
  .service-list li { display: inline-block; margin: 0 7px; }
  .service-list li::before {
    content: "";
    display: inline-block;
    width: 6px; height: 6px;
    border-radius: 50%;
    background: var(--brand-red);
    margin-right: 9px;
    vertical-align: 2px;
  }
</style>
</head>
<body>
  <section class="card card-front" aria-label="Business card front">
    <div class="wordmark">Brenwick<br>Casing Services</div>
    <p class="holder-name">Cody Hallman</p>
    <p class="holder-title">Area Manager</p>
    <div class="divider"></div>
    <p class="address">Redmesa,&nbsp; OK 73999</p>
    <ul class="contact-list">
      <li>(555) 410-2700<svg viewBox="0 0 10 10" aria-label="Office"><path d="M1 3.5C1 2 3 1.5 5 1.5S9 2 9 3.5V4.5H7V3.6H3V4.5H1Z"/><rect x="2" y="5" width="6" height="4" rx="1"/></svg></li>
      <li>(555) 410-2731<svg viewBox="0 0 10 10" aria-label="Fax"><rect x="2.5" y="0.5" width="5" height="3"/><rect x="0.5" y="3.5" width="9" height="5" rx="1"/><rect x="2.5" y="6.5" width="5" height="3" fill="#fff"/></svg></li>
      <li>(555) 287-6142<svg viewBox="0 0 10 10" aria-label="Cell"><path d="M3 0.5h4a1 1 0 0 1 1 1v7a1 1 0 0 1-1 1H3a1 1 0 0 1-1-1v-7a1 1 0 0 1 1-1Zm0.2 1.3v5.6h3.6V1.8Z"/></svg></li>
      <li>codyhallman@brenwickcasing.com<svg viewBox="0 0 10 10" aria-label="Email"><rect x="0.5" y="2" width="9" height="6.5"/><path d="M0.8 2.3 5 5.8 9.2 2.3" fill="none" stroke="#fff" stroke-width="0.9"/></svg></li>
    </ul>
  </section>

  <section class="card card-back" aria-label="Business card back">
    <div class="wordmark">Brenwick<br>Casing Services</div>
    <ul class="service-list row-one">
      <li>External CRT</li><li>Internal CRT</li><li>Casing Crews</li>
    </ul>
    <ul class="service-list row-two">
      <li>Torque Turn</li><li>Laydown Machine</li>
    </ul>
  </section>
</body>
</html>
```